Landscaping flier 2024

Create a 1 page flier for landscaping services
1. Must be completed in Adobe Photoshop
2. Size 8.5" x 11" (portrait layout)
3. Include logo
4. Text to include:
2024 Gravesite Landscaping Packages
info@hollowbrookmemorial.org
(201) 555-0148
hollowbrookmemorial.org
5. Use chart text for the content. DO NOT COPY THE CHART DESIGN/FORMAT. Use the chart for the text you need only.
6. Use "Pricing cards as format for laying out the chart". Open to other ideas as well.
**Use the example of chart design (handwritten) to base your design off of.
7. Photos
-include before and after care photos

```html
<!DOCTYPE html>
<html lang="en">
<head>
<meta charset="utf-8">
<title>2024 Gravesite Landscaping Packages</title>
<link href="https://fonts.googleapis.com/css2?family=Cinzel:wght@700;800&family=Montserrat:wght@400;500;600;700;800&display=swap" rel="stylesheet">
<style>
  :root{
    --bg:#e9e9e9;
    --paper:#ffffff;
    --maroon:#8e1f34;
    --maroon-deep:#6f1526;
    --crimson:#b3263f;
    --navy:#233246;
    --navy-deep:#1b2838;
    --blue:#2f5479;
    --blue-light:#3e6b96;
    --gold:#e0b84a;
    --green:#5cb946;
    --red:#d8413b;
    --ink:#2a2a2a;
    --grey-text:#555;
  }
  *{box-sizing:border-box;margin:0;padding:0}
  html,body{width:1200px;height:2415px;overflow:hidden;background:var(--bg)}
  body{font-family:"Montserrat",Arial,sans-serif;position:relative}
  .flier{position:absolute;left:160px;top:627px;width:880px;height:1160px;background:var(--paper);overflow:hidden;box-shadow:0 10px 30px rgba(0,0,0,.18)}
  .hero-photo{position:absolute;left:0;top:0;width:880px;height:385px;background:linear-gradient(180deg,#f4f4f4 0%,#d9d9d9 45%,#9a9ea3 75%,#c9cbcd 100%)}
  .title{position:absolute;left:0;top:32px;width:880px;text-align:center;font-family:"Cinzel",Georgia,serif;font-weight:800;color:var(--maroon);line-height:1.3}
  .title .line1{font-size:34px;display:block}
  .title .line2{font-size:36px;display:block}
  .title-rule{position:absolute;top:150px;height:2px;background:var(--maroon);width:90px}
  .title-dot{position:absolute;left:432px;top:143px;width:16px;height:16px;border:2px solid var(--navy);border-radius:50%}
  .swoosh{position:absolute;left:0;top:330px}
  .card{position:absolute;color:#fff;overflow:hidden}
  .card-seasonal{left:37px;top:380px;width:262px;height:525px;background:var(--navy)}
  .card-perpetual{left:300px;top:355px;width:280px;height:570px;background:var(--maroon);box-shadow:0 0 18px rgba(0,0,0,.3);z-index:2}
  .card-basic{left:581px;top:380px;width:262px;height:505px;background:var(--navy)}
  .card-head{height:110px;padding-top:22px;text-align:center;background:linear-gradient(180deg,var(--blue-light),var(--blue))}
  .card-perpetual .card-head{background:linear-gradient(180deg,#c23050,var(--crimson));height:115px;padding-top:30px}
  .card-name{font-weight:800;font-size:20px;line-height:1.05;letter-spacing:.3px}
  .card-sub{font-size:9.5px;line-height:1.25;margin-top:5px;opacity:.9;text-transform:uppercase}
  .head-notch{display:block;margin:8px auto 0;width:10px;height:10px;border:1.5px solid #fff;border-radius:50%}
  .ribbon{position:absolute;left:-30px;top:14px;width:120px;height:18px;background:var(--gold);color:var(--maroon-deep);font-size:7.5px;font-weight:800;text-align:center;line-height:18px;transform:rotate(-38deg)}
  .price-block{height:115px;display:flex;align-items:center;justify-content:center;gap:10px;flex-wrap:wrap;padding:18px 10px 0}
  .price-label{font-size:9px;font-weight:700;line-height:1.2;text-align:right;text-transform:uppercase}
  .price{font-size:44px;font-weight:600;line-height:1}
  .price sup{font-size:20px;vertical-align:18px}
  .price-note{width:100%;text-align:center;font-size:10px;opacity:.85;margin-top:-6px}
  .years{display:flex;gap:6px;align-items:flex-start}
  .year{text-align:center}
  .year-dot{width:34px;height:34px;border-radius:50%;background:var(--blue-light);display:flex;flex-direction:column;align-items:center;justify-content:center;font-weight:700;font-size:15px;line-height:1}
  .year-dot small{font-size:5.5px;font-weight:600;text-transform:uppercase}
  .year-cost{font-size:11px;font-weight:600;margin-top:4px}
  .year-cost sup{font-size:7px}
  .years-note{font-size:9px;line-height:1.25;width:80px;opacity:.9}
  .schedule{display:flex;gap:10px;align-items:center;padding:9px 14px;background:rgba(0,0,0,.22);font-size:8.5px;line-height:1.25}
  .schedule b{font-weight:800;text-transform:uppercase;font-size:8px;min-width:70px}
  .card-perpetual .schedule{background:rgba(0,0,0,.18)}
  .features{list-style:none;padding:22px 0 0 34px}
  .features li{position:relative;font-size:12.5px;line-height:1.2;margin-bottom:14px}
  .features li::before{content:"";position:absolute;left:-16px;top:3px;width:9px;height:9px;border-radius:50%;background:var(--red)}
  .features li.yes::before{background:var(--green)}
  .brand{position:absolute;left:40px;top:985px;display:flex;align-items:center;gap:14px}
  .brand-mark{width:56px;height:56px;border-radius:50%;background:#d9d9d9}
  .brand-name{font-family:"Cinzel",Georgia,serif;font-weight:700;font-size:27px;color:var(--maroon);letter-spacing:.5px}
  .contacts{position:absolute;left:118px;top:1060px;list-style:none}
  .contacts li{display:flex;align-items:center;gap:12px;font-size:15px;color:var(--ink);margin-bottom:13px}
  .contacts li.phone{font-weight:700;font-size:17px}
  .contacts svg{width:14px;height:14px;flex:none}
  .care-photo{position:absolute;top:985px;width:170px;height:150px}
  .care-before{left:492px}
  .care-after{left:677px}
  .care-photo .fill{position:absolute;inset:0;background:linear-gradient(180deg,#9aa39a 0%,#6f8a5d 40%,#5e9b3a 75%,#4f8a30 100%)}
  .care-tag{position:absolute;left:32px;top:-10px;padding:4px 12px;background:var(--maroon);color:#fff;font-size:10px;font-style:italic;font-weight:600;border-radius:2px}
</style>
</head>
<body>
<main class="flier">
  <div class="hero-photo" role="img" aria-label="Photo of a snowy cemetery with headstones and a historic house behind bare trees"></div>
  <h1 class="title"><span class="line1">2024 Gravesite</span><span class="line2">Landscaping Packages</span></h1>
  <span class="title-rule" style="left:330px"></span>
  <span class="title-dot"></span>
  <span class="title-rule" style="left:460px"></span>

  <svg class="swoosh" width="880" height="60" viewBox="0 0 880 60" aria-hidden="true">
    <path d="M0 30 Q220 10 440 30 T880 0 L880 60 L0 60 Z" fill="#8e1f34"/>
    <path d="M0 42 Q230 22 440 40 T880 14 L880 60 L0 60 Z" fill="#ffffff"/>
  </svg>

  <section class="card card-seasonal">
    <header class="card-head">
      <div class="card-name">SEASONAL CARE</div>
      <div class="card-sub">Seasonal landscaping<br>grave care</div>
      <span class="head-notch"></span>
    </header>
    <div class="price-block">
      <div class="years">
        <div class="year"><div class="year-dot">1<small>year</small></div><div class="year-cost"><sup>$</sup>132</div></div>
        <div class="year"><div class="year-dot">3<small>years</small></div><div class="year-cost"><sup>$</sup>396</div></div>
        <div class="year"><div class="year-dot">2<small>years</small></div><div class="year-cost"><sup>$</sup>264</div></div>
      </div>
      <div class="years-note">Multi-year payment locks in current rates</div>
    </div>
    <div class="schedule"><b>Weeding &amp; trimming on your gravesite</b><span>Approximately every 7 weeks during the growing season mid-April through mid-October</span></div>
    <ul class="features">
      <li>Payment Ensures<br>Grave Care Forever</li>
      <li>Monument Leveling</li>
      <li>Monument Cleaning</li>
      <li>Full Bed Of Boxwood Shrubs</li>
      <li>Replacement Of Shrubs</li>
      <li>Trust Certificate</li>
    </ul>
  </section>

  <section class="card card-perpetual">
    <div class="ribbon">MOST POPULAR</div>
    <header class="card-head">
      <div class="card-name">PERPETUAL CARE<br>ENDOWMENT</div>
      <div class="card-sub">Landscaping care forever<br>for graves with plantings</div>
      <span class="head-notch"></span>
    </header>
    <div class="price-block">
      <div class="price-label">12 monthly<br>payments of</div>
      <div class="price"><sup>$</sup>351</div>
      <div class="price-note">Call for single payment discount</div>
    </div>
    <div class="schedule"><b>Weeding &amp; trimming on your gravesite</b><span>Approximately every 7 weeks during the growing season mid-April through mid-October</span></div>
    <ul class="features">
      <li class="yes">Payment Ensures<br>Grave Care Forever</li>
      <li class="yes">Monument Leveling</li>
      <li class="yes">Monument Cleaning</li>
      <li class="yes">Full Bed Of Boxwood Shrubs</li>
      <li class="yes">Replacement Of Shrubs</li>
      <li class="yes">Trust Certificate</li>
    </ul>
  </section>

  <section class="card card-basic">
    <header class="card-head">
      <div class="card-name">BASIC CARE<br>ENDOWMENT</div>
      <div class="card-sub">Landscaping care forever<br>for graves with no plantings</div>
      <span class="head-notch"></span>
    </header>
    <div class="price-block">
      <div class="price-label">12 monthly<br>payments of</div>
      <div class="price"><sup>$</sup>287</div>
      <div class="price-note">Call for single payment discount</div>
    </div>
    <div class="schedule"><b>Weeding &amp; trimming on your gravesite</b><span>2 times per year:<br>mid-May &amp; mid-September</span></div>
    <ul class="features">
      <li class="yes">Payment Ensures<br>Grave Care Forever</li>
      <li class="yes">Monument Leveling</li>
      <li class="yes">Monument Cleaning</li>
      <li>Full Bed Of Boxwood Shrubs</li>
      <li>Replacement Of Shrubs</li>
      <li>Trust Certificate</li>
    </ul>
  </section>

  <div class="brand">
    <span class="brand-mark"></span>
    <span class="brand-name">Hollowbrook Memorial</span>
  </div>

  <ul class="contacts">
    <li class="phone"><svg viewBox="0 0 16 16" aria-hidden="true"><path d="M3 1.5l3 .5 1 3.5-2 1.3a9 9 0 0 0 4.2 4.2l1.3-2 3.5 1 .5 3-2 1.5C6.5 14 2 9.5 1.5 3.5z" fill="none" stroke="#8e1f34" stroke-width="1.4"/></svg>(201) 555-0148</li>
    <li><svg viewBox="0 0 16 16" aria-hidden="true"><rect x="1.5" y="3.5" width="13" height="9" rx="1" fill="none" stroke="#8e1f34" stroke-width="1.4"/><path d="M1.5 4l6.5 5 6.5-5" fill="none" stroke="#8e1f34" stroke-width="1.4"/></svg>info@hollowbrookmemorial.org</li>
    <li><svg viewBox="0 0 16 16" aria-hidden="true"><circle cx="8" cy="8" r="6.5" fill="none" stroke="#8e1f34" stroke-width="1.4"/><path d="M1.5 8h13M8 1.5c-3 3.5-3 9.5 0 13M8 1.5c3 3.5 3 9.5 0 13" fill="none" stroke="#8e1f34" stroke-width="1.2"/></svg>www.hollowbrookmemorial.org</li>
  </ul>

  <figure class="care-photo care-before">
    <div class="fill" role="img" aria-label="Before care photo of an overgrown gravesite with shrubs on green lawn"></div>
    <figcaption class="care-tag">Before Care</figcaption>
  </figure>
  <figure class="care-photo care-after">
    <div class="fill" role="img" aria-label="After care photo of a trimmed gravesite with neat boxwood bed"></div>
    <figcaption class="care-tag">After care</figcaption>
  </figure>
</main>
</body>
</html>
```